Carpet cleaning company focused on high quality needs business cards

We are a growing company that just merged with another company and need to design a new business card. We do both residential as well as commercial cleaning. We do carpet, tile & grout, upholstery, hard floors, and stain & pet odor removal. We treat our customers like family and strive to achieve outstanding results with every job.

```html
<!DOCTYPE html>
<html lang="en">
<head>
<meta charset="utf-8">
<title>Mack's Fresh Crew Cleaning – Business Card</title>
<link rel="stylesheet" href="https://fonts.googleapis.com/css2?family=Open+Sans:wght@400;600;800&display=swap">
<style>
  :root {
    --stage: #e9e9e9;
    --card-black: #050505;
    --brand-red: #ef443f;
    --paper: #ffffff;
    --ink-light: #ffffff;
    --mascot-blue: #1b86c6;
    --mascot-tan: #c49a5a;
    --mascot-skin: #f3dfc4;
  }
  * { box-sizing: border-box; margin: 0; padding: 0; }
  html, body {
    width: 1200px; height: 900px; overflow: hidden;
    background: var(--stage);
    font-family: "Open Sans", Arial, sans-serif;
  }
  .canvas { position: relative; width: 1200px; height: 900px; }
  .card {
    position: absolute; left: 250px;
    width: 700px; height: 400px;
    border-radius: 26px; overflow: hidden;
  }

  /* Front */
  .card--front { top: 34px; background: var(--card-black); }
  .front__mascot {
    position: absolute; left: 120px; top: 70px;
    width: 220px; height: 260px;
    background: linear-gradient(180deg, var(--mascot-blue) 0%, var(--mascot-tan) 60%, var(--brand-red) 100%);
  }
  .front__name {
    position: absolute; left: 370px; top: 120px;
    color: var(--ink-light); font-weight: 800; line-height: 1;
  }
  .front__name .name-main { display: block; font-size: 88px; letter-spacing: -2px; }
  .front__name .name-sub  { display: block; font-size: 34px; letter-spacing: 0.5px; margin-top: 4px; }

  /* Back */
  .card--back {
    top: 466px;
    background: linear-gradient(90deg, var(--paper) 0 38%, var(--brand-red) 38% 100%);
  }
  .back__mascot {
    position: absolute; left: 40px; top: 50px;
    width: 430px; height: 300px; border-radius: 18px;
    background: linear-gradient(135deg, var(--mascot-skin) 0%, var(--mascot-blue) 45%, var(--mascot-tan) 100%);
  }
  .back__contact {
    position: absolute; right: 40px; top: 50%;
    writing-mode: vertical-rl; transform: translateY(-50%) rotate(180deg);
    color: var(--ink-light);
    display: flex; flex-direction: column; align-items: center;
  }
  .contact__name { font-size: 34px; font-weight: 600; line-height: 1.05; letter-spacing: 0.5px; }
  .contact__title { font-size: 20px; font-weight: 400; line-height: 1.2; }
  .contact__icons {
    display: flex; align-items: center; gap: 8px;
    margin: 12px 0;
  }
  .contact__icons::before, .contact__icons::after {
    content: ""; width: 1px; height: 22px; background: var(--ink-light);
  }
  .icon {
    width: 24px; height: 24px; border-radius: 50%;
    background: var(--ink-light);
    display: flex; align-items: center; justify-content: center;
  }
  .icon svg { width: 14px; height: 14px; }
  .contact__lines { font-size: 17px; line-height: 1.45; text-align: center; }
</style>
</head>
<body>
<main class="canvas">

  <section class="card card--front">
    <div class="front__mascot" role="img" aria-label="Cartoon mascot of a smiling cleaner with a steam wand standing on a red rug"></div>
    <div class="front__name">
      <span class="name-main">Mack's</span>
      <span class="name-sub">FRESH CREW</span>
      <span class="name-sub">CLEANING</span>
    </div>
  </section>

  <section class="card card--back">
    <div class="back__mascot" role="img" aria-label="Large cartoon cleaner leaping with a carpet-cleaning wand and hose"></div>
    <div class="back__contact">
      <p class="contact__name">DANIEL REYES</p>
      <p class="contact__title">Founder &amp; CEO</p>
      <div class="contact__icons">
        <span class="icon" aria-label="Phone">
          <svg viewBox="0 0 24 24"><path fill="#ef443f" d="M6.6 10.8a15 15 0 0 0 6.6 6.6l2.2-2.2c.3-.3.7-.4 1-.2 1.1.4 2.3.6 3.6.6.6 0 1 .4 1 1V20c0 .6-.4 1-1 1A17 17 0 0 1 3 4c0-.6.4-1 1-1h3.5c.6 0 1 .4 1 1 0 1.3.2 2.5.6 3.6.1.3 0 .7-.2 1z"/></svg>
        </span>
        <span class="icon" aria-label="Email">
          <svg viewBox="0 0 24 24"><rect x="3" y="6" width="18" height="12" rx="1" fill="#ef443f"/><path d="M3 6l9 7 9-7" fill="none" stroke="#fff" stroke-width="1.6"/></svg>
        </span>
        <span class="icon" aria-label="Website">
          <svg viewBox="0 0 24 24" fill="none" stroke="#ef443f" stroke-width="2"><circle cx="12" cy="12" r="9"/><path d="M3 12h18M12 3c3 3 3 15 0 18M12 3c-3 3-3 15 0 18"/></svg>
        </span>
      </div>
      <p class="contact__lines">(555) 217-0394<br>hello@freshcrewclean.com<br>freshcrewclean.com</p>
    </div>
  </section>

</main>
</body>
</html>
```